Single-sided business card for restaurant velmora with new logo made on this site

Business card options with new logo including restaurant name, address, phone number and website. This business card is single-sided only and will be presented at the hostess desk for clients to take. I would like to see options based on a cream card background, a white card background, a yellow card background and a burgundy colored background. It needs to be elegant and traditional.

Target Market(s)

local and international crowd

Industry/Entity Type

restaurant

Contact Information for Business Card

address, website and phone number

Font styles to use
Serif

Colors
EE7325
F08F49
F5BC92
FAE3D3
FDF4ED

Requirements
Must have
• new logo, address, phone number, website
Should not have
• more than three colors

```html
<!DOCTYPE html>
<html lang="es">
<head>
<meta charset="utf-8">
<title>Velmora – Tarjeta de presentación</title>
<link rel="stylesheet" href="https://fonts.googleapis.com/css2?family=Cinzel:wght@400;500&family=Cormorant+Garamond:wght@500&family=Arimo:wght@400&display=swap">
<style>
  :root {
    --stage: #2a2a2b;
    --card: #f7b52f;
    --ink: #4a1915;
    --rule: #7a3a1c;
  }
  * { margin: 0; padding: 0; box-sizing: border-box; }
  html, body { width: 1200px; height: 820px; overflow: hidden; }
  body {
    background: var(--stage);
    display: flex;
    align-items: center;
    justify-content: center;
  }
  .business-card {
    position: relative;
    width: 1000px;
    height: 571px;
    background: var(--card);
    color: var(--ink);
  }
  .contact {
    position: absolute;
    left: 92px;
    top: 118px;
    width: 440px;
  }
  .reservations-label {
    font-family: "Cinzel", serif;
    font-size: 34px;
    font-weight: 500;
    letter-spacing: 0.04em;
    line-height: 1;
  }
  .phone {
    font-family: "Cormorant Garamond", serif;
    font-size: 62px;
    font-weight: 500;
    letter-spacing: 0.02em;
    line-height: 1;
    margin-top: 4px;
  }
  .divider {
    height: 2px;
    width: 330px;
    margin: 20px 0 26px;
    background: linear-gradient(90deg, rgba(122,58,28,0) 0%, var(--rule) 45%, rgba(122,58,28,0) 100%);
  }
  .website,
  .address {
    font-family: "Arimo", sans-serif;
    font-size: 29px;
    line-height: 1.25;
  }
  .address { list-style: none; }
  .brand-name {
    position: absolute;
    left: 610px;
    top: 230px;
    width: 320px;
    text-align: center;
    font-family: "Cinzel", serif;
    font-size: 58px;
    font-weight: 500;
    letter-spacing: 0.14em;
    color: var(--ink);
  }
</style>
</head>
<body>
  <section class="business-card">
    <div class="contact">
      <p class="reservations-label">Reservaciones</p>
      <p class="phone">958-412-3070</p>
      <div class="divider"></div>
      <p class="website">www.velmora.com.mx</p>
      <div class="divider"></div>
      <ul class="address">
        <li>Restaurant Velmora</li>
        <li>Calle Jazmín 418</li>
        <li>Santa Lucía del Mar</li>
        <li>Oaxaca CP 70420</li>
      </ul>
    </div>
    <p class="brand-name">VELMORA</p>
  </section>
</body>
</html>
```